New Innovative Counselling and psychotherapy Service needs Business Card design

Keep it simple and professional. On one side, just company name and logo (perhaps in all blue) and maybe a tag line.

On other side (all white) my name and Qualifications in centre

Industry/Entity Type

Health And Wellness

Contact Information for Business Card

Dara Whelby
Counsellor & Psychotherapist
BSc (Psychol.), BA, Dip. (Couns. & Psych.), PG.Cert (CBT), FGTrK, ONRE

I will also require Mobile no, Email and web site address of which I'll pass on to final designer.

Font styles to use
Sans Serif

Requirements
Must have
• My Logo Only and please use the colours in logo that is in it.
Should not have
• Any other images

```html
<!DOCTYPE html>
<html lang="en">
<head>
<meta charset="utf-8">
<title>Brightwell Path – Business Card</title>
<link rel="stylesheet" href="https://fonts.googleapis.com/css2?family=Roboto:wght@300;400;500;700&display=swap">
<style>
  :root {
    --backdrop: #e8e8ea;
    --card-white: #ffffff;
    --brand-blue: #3fa9e5;
    --brand-teal: #63bfc4;
    --brand-green: #8dcb58;
    --ink: #333538;
    --ink-soft: #4a4c50;
  }
  * { box-sizing: border-box; margin: 0; padding: 0; }
  html, body {
    width: 1200px; height: 726px; overflow: hidden;
    background: var(--backdrop);
    font-family: "Roboto", Arial, sans-serif;
  }
  .canvas {
    position: relative; width: 1200px; height: 726px;
    display: flex; align-items: center; justify-content: center; gap: 40px;
  }
  .card {
    position: relative; width: 540px; height: 309px;
    border-radius: 3px; overflow: hidden;
    box-shadow: 0 10px 24px rgba(0,0,0,0.12), 0 2px 4px rgba(0,0,0,0.08);
  }
  /* Front */
  .card--front {
    background: linear-gradient(120deg, var(--brand-blue) 0%, var(--brand-teal) 45%, var(--brand-green) 100%);
    display: flex; align-items: center; justify-content: center;
  }
  .front-title {
    color: var(--card-white); font-weight: 300; font-size: 46px; letter-spacing: 1px;
  }
  /* Back */
  .card--back { background: var(--card-white); }
  .identity { position: absolute; left: 34px; top: 98px; }
  .identity__name {
    color: var(--brand-blue); font-weight: 700; font-size: 21px; margin-bottom: 6px;
  }
  .identity__role, .identity__quals {
    color: var(--ink-soft); font-size: 12px; line-height: 1.35;
  }
  .brand-mark {
    position: absolute; right: 36px; top: 86px;
    display: flex; flex-direction: column; align-items: center; gap: 12px;
  }
  .brand-mark__dot {
    width: 58px; height: 58px; border-radius: 50%; background: var(--brand-blue);
  }
  .brand-mark__name { color: var(--ink); font-weight: 400; font-size: 20px; }
  .contact { position: absolute; left: 34px; bottom: 42px; list-style: none; }
  .contact__item {
    display: flex; align-items: center; gap: 10px;
    color: var(--ink); font-size: 13px; line-height: 1.6;
  }
  .contact__icon { width: 13px; height: 13px; flex: none; }
  .stripe {
    position: absolute; left: 0; right: 0; bottom: 0; height: 8px; display: flex;
  }
  .stripe__blue { flex: 0 0 67%; background: var(--brand-blue); }
  .stripe__green { flex: 1; background: var(--brand-green); }
</style>
</head>
<body>
<main class="canvas">
  <section class="card card--front" aria-label="Card front">
    <h1 class="front-title">Brightwell Path</h1>
  </section>

  <section class="card card--back" aria-label="Card back">
    <div class="identity">
      <h2 class="identity__name">Dara Whelby</h2>
      <p class="identity__role">Counsellor &amp; Psychotherapist</p>
      <p class="identity__quals">BSc (Psychol.), BA, Dip. (Couns. &amp; Psych.),<br>PG.Cert (CBT), FGTrK, ONRE</p>
    </div>

    <div class="brand-mark">
      <span class="brand-mark__dot"></span>
      <span class="brand-mark__name">Brightwell Path</span>
    </div>

    <ul class="contact">
      <li class="contact__item">
        <svg class="contact__icon" viewBox="0 0 16 16" aria-hidden="true"><path fill="#3aa6a0" d="M3 1h3l1.5 4-2 1.2a9 9 0 0 0 4.3 4.3L11 8.5l4 1.5v3c0 1-1 2-2 2A13 13 0 0 1 1 3c0-1 1-2 2-2z"/></svg>
        0123 456 7000
      </li>
      <li class="contact__item">
        <svg class="contact__icon" viewBox="0 0 16 16" aria-hidden="true"><rect x="1" y="3" width="14" height="10" rx="1" fill="#3aa6a0"/><path d="M1.5 3.8 8 9l6.5-5.2" fill="none" stroke="#fff" stroke-width="1.3"/></svg>
        dara.w@BrightwellPath.com
      </li>
      <li class="contact__item">
        <svg class="contact__icon" viewBox="0 0 16 16" aria-hidden="true"><circle cx="8" cy="8" r="7" fill="#3aa6a0"/><path d="M1 8h14M8 1c-3 3.5-3 10.5 0 14M8 1c3 3.5 3 10.5 0 14" fill="none" stroke="#fff" stroke-width="1"/></svg>
        www.BrightwellPath.com
      </li>
    </ul>

    <div class="stripe"><span class="stripe__blue"></span><span class="stripe__green"></span></div>
  </section>
</main>
</body>
</html>
```